TuneRoost - Music Industry App needs a top quality wordpress homepage

We need a modern responsive wordpress homepage built. Our website will only feature one page with the goal to get people to sign up to our app. A word document has been uploaded outlining the page content/sections.

Once the homepage is finalised, I will also need 2 landing pages built as part of this competition. It will be very similar to the homepage with the same layout etc but just feature different images and content. The homepage is for anyone (artists and venues) to find out about us but the landing pages will be artist or venue specific.

The completed work must be delivered as an exportable file into wordpress and be designed properly so no more work is needed to begin utilising as the actual website. The images used must be setup correctly for speed and quality also.

Target Market(s)

Venues and Artists.

Coding

Coded - Design and coding required

Requirements
Must have
• UPDATE: High Res Logo files attached
• Must be a modern looking website and be responsive. Must look good across all devices from desktop, to mobile and tablet. Needs to be very high quality.
• Please see the attached logo - I am waiting for the final high quality version and will reupload when complete but this will be enough to get you started for now. The website must have a dark base colour and have red/white elements to match the logo. The red colour used MUST match the red colour used in the logo.
• Please have a go at creating it how you think is best and provide feedback from there. I am leaving it very open to the designers so I can get the best website possible and lots of different ideas etc.

```html
<!DOCTYPE html>
<html lang="en">
<head>
<meta charset="utf-8">
<title>TuneRoost – Live Music Booking</title>
<link href="https://fonts.googleapis.com/css2?family=Montserrat:wght@300;400;500;600;700&family=Lato:wght@400;700&display=swap" rel="stylesheet">
<style>
:root{
  --red:#e3101b;
  --black:#000;
  --white:#fff;
  --font-head:'Montserrat',sans-serif;
  --font-body:'Lato',sans-serif;
}
*{box-sizing:border-box;margin:0;padding:0}
html,body{width:1200px;height:5391px;overflow:hidden;background:var(--black);color:var(--white);font-family:var(--font-body)}
.page{position:relative;width:1200px;height:5391px;overflow:hidden}
.abs{position:absolute}
.brand{font-family:var(--font-head);font-weight:500;color:var(--red);display:flex;align-items:center;gap:10px}
.brand .dot{width:18px;height:18px;border-radius:50%;background:var(--white)}
/* plain divider bands */
.band{position:absolute;left:0;width:1200px}
.band-black{background:var(--black)}
.band-red{background:var(--red)}
/* header */
.site-header{position:absolute;left:0;top:0;width:1200px;height:176px;background:var(--black);z-index:3}
.search{left:163px;top:36px;width:250px;height:42px;background:var(--white);border-radius:21px;color:#999;font-size:14px;padding:12px 18px}
.search .btn{position:absolute;right:5px;top:5px;width:32px;height:32px;border-radius:50%;background:var(--red)}
.header-logo{left:0;width:1200px;top:50px;justify-content:center;font-size:46px}
.callus{left:885px;top:34px;font-family:var(--font-head);font-size:16px}
.callus small{display:block;color:var(--red);font-size:13px;font-weight:600}
.callus svg{position:absolute;left:-50px;top:4px}
.nav{top:126px;font-family:var(--font-head);font-size:16px;font-weight:500;color:var(--white)}
/* hero */
.hero-media{left:0;top:176px;width:1200px;height:600px;background:radial-gradient(ellipse at 50% 10%,#7a5a78 0%,#3b2a3a 30%,#140d12 65%,#050505 100%)}
.hero-title{left:0;top:318px;width:1200px;text-align:center;font-family:var(--font-head)}
.hero-title h1{font-size:54px;font-weight:500}
.hero-title p{font-size:32px;font-weight:400;line-height:47px;margin-top:8px}
.pill{display:inline-flex;align-items:center;gap:10px;border-radius:30px;font-family:var(--font-head);font-weight:700;font-size:16px;padding:0 22px 0 34px;height:52px;position:absolute}
.pill .arrow{width:16px;height:16px;border-radius:50%;background:currentColor;position:relative}
.pill .arrow::after{content:"";position:absolute;left:5px;top:4px;border:4px solid transparent;border-left:6px solid var(--red)}
.pill.red{background:var(--red);color:var(--white)}
.pill.white{background:var(--white);color:var(--red)}
.pill.white .arrow::after{border-left-color:var(--white)}
/* welcome */
.section-title{font-family:var(--font-head);font-weight:300;font-size:36px;color:var(--white)}
.section-title b{color:var(--red);font-weight:700}
.center{text-align:center;left:0;width:1200px}
.lead{left:150px;width:900px;text-align:center;font-size:14px;line-height:36px;color:var(--white)}
.field{top:1074px;width:226px;height:42px;background:var(--white);color:#666;font-size:13px;padding:13px 10px}
.field i{position:absolute;right:12px;top:13px;width:14px;height:14px;background:var(--red);border-radius:3px}
.rule{left:150px;width:960px;height:1px;background:#2a2a2a}
.how-bg{left:0;top:1180px;width:1200px;height:900px;background:linear-gradient(180deg,#000 0%,#1a1012 50%,#0d0709 100%)}
.how-label{font-family:var(--font-head);font-weight:700;font-size:15px;line-height:31px}
.node{width:104px;height:104px;border-radius:50%;background:var(--red);border:6px solid var(--white);display:flex;align-items:center;justify-content:center}
/* split */
.venues{left:0;top:2080px;width:600px;height:780px;background:var(--red)}
.artists{left:600px;top:2080px;width:600px;height:780px;background:linear-gradient(180deg,#1c0f12,#0a0506)}
.split h2{font-family:var(--font-head);font-size:36px;font-weight:700}
.split p{font-size:13px;line-height:33px;text-align:justify}
.split ul{list-style:none;font-size:12px;line-height:45px}
.split li::before{content:"";display:inline-block;width:9px;height:9px;border:2px solid currentColor;border-radius:50%;margin-right:12px;vertical-align:middle}
.artists-text{color:#cfcfcf}
/* why */
.why-bg{left:0;top:2860px;width:1200px;height:1100px;background:linear-gradient(180deg,#0b0b0b,#121212 50%,#050505)}
.photo{border-radius:50%}
.why-list{font-size:15px;line-height:32px;color:var(--white)}
.why-list b{color:var(--red);font-weight:400}
.about-text{font-size:15px;line-height:31.5px;text-align:justify}
/* contact */
.map{left:0;top:3960px;width:600px;height:730px;background:linear-gradient(160deg,#e9ecef,#d7dcd4 60%,#cfd6cc)}
.contact{left:600px;top:3960px;width:600px;height:730px;background:var(--red)}
.address-card{left:222px;top:4194px;width:312px;height:222px;background:var(--red);padding:18px 48px;font-family:var(--font-head)}
.address-card h4{font-size:19px;font-weight:600;margin-top:6px}
.address-card p{font-size:21px;line-height:35px}
.cf-line{left:642px;width:466px;height:2px;background:rgba(255,255,255,.7)}
.cf-label{left:648px;font-family:var(--font-head);font-size:16px;font-weight:500}
/* footer */
.footer-icon{width:84px;height:84px;border-radius:50%;background:var(--red);border:3px solid var(--white);display:flex;align-items:center;justify-content:center}
.footer-info{font-family:var(--font-head);font-size:16px;line-height:28px;text-align:center}
.footer-links{font-family:var(--font-head);font-size:15px}
.social{width:30px;height:30px;border-radius:50%;border:2px solid var(--white)}
</style>
</head>
<body>
<div class="page">

<header class="site-header">
  <div class="abs search">Search<span class="btn"></span></div>
  <div class="abs brand header-logo"><span class="dot"></span>TuneRoost</div>
  <div class="abs callus">
    <svg width="36" height="36" viewBox="0 0 24 24"><path fill="#e3101b" d="M6.6 10.8a15 15 0 006.6 6.6l2.2-2.2a1 1 0 011-.25 11.4 11.4 0 003.6.6 1 1 0 011 1V20a1 1 0 01-1 1A17 17 0 013 4a1 1 0 011-1h3.5a1 1 0 011 1c0 1.25.2 2.45.6 3.6a1 1 0 01-.25 1z"/></svg>
    <small>CALL US:</small>555 010 2040</div>
  <nav>
    <span class="abs nav" style="left:97px">HOME</span>
    <span class="abs nav" style="left:186px">HOW IT WORKS</span>
    <span class="abs nav" style="left:355px">WHY TUNEROOST?</span>
    <span class="abs nav" style="left:745px">VENUES &amp; ARTIST</span>
    <span class="abs nav" style="left:928px">ABOUT</span>
    <span class="abs nav" style="left:1024px">CONTACT</span>
  </nav>
</header>

<div class="abs hero-media" role="img" aria-label="Crowd at a live concert under stage lights"></div>
<div class="abs hero-title">
  <h1>Zoomly for Live Music</h1>
  <p>TuneRoost connects venues with artists to<br>make booking gigs simple</p>
</div>
<a class="pill red" style="left:464px;top:502px">Sign up now for FREE<span class="arrow"></span></a>

<div class="band band-red" style="top:770px;height:6px"></div>

<h2 class="abs section-title center" style="top:872px">Welcome to <b>TuneRoost</b></h2>
<p class="abs lead" style="top:932px">Sed ut perspiciatis unde omnis iste natus error sit voluptatem accusantium doloremque laudantium, totam rem aperiam, eaque ipsa quae ab illo inventore veritatis et quasi architecto beatae vitae dicta sunt explicabo. Nemo enim ipsam voluptatem quia voluptas sit aspernatur aut odit aut fugit, voluptatem sequi nesciunt.</p>
<div class="abs field" style="left:104px">Full Name<i></i></div>
<div class="abs field" style="left:359px">Phone Number<i></i></div>
<div class="abs field" style="left:615px">Email Address<i></i></div>
<div class="abs" style="left:870px;top:1074px;width:226px;height:42px;background:var(--red);font-family:var(--font-head);font-weight:600;font-size:14px;text-align:center;line-height:42px">➤ Sign Up Now for Free</div>
<div class="abs rule" style="top:1196px"></div>

<div class="abs how-bg" role="img" aria-label="Dim photo of a musician in a studio" style="z-index:-1"></div>
<h2 class="abs section-title center" style="top:1268px">How <b>TuneRoost Works</b></h2>
<svg class="abs" style="left:354px;top:1365px" width="494" height="494" viewBox="0 0 494 494">
  <circle cx="247" cy="247" r="247" fill="#e3101b"/>
  <circle cx="247" cy="247" r="170" fill="#3a0508"/>
</svg>
<div class="abs brand" style="left:0;width:1200px;top:1590px;justify-content:center;font-size:38px;color:var(--white)"><span class="dot" style="background:var(--red)"></span>TuneRoost</div>
<div class="abs node" style="left:330px;top:1444px"><svg width="44" height="44" viewBox="0 0 24 24" fill="#fff"><circle cx="9" cy="7" r="4"/><path d="M2 20c0-4 3-6 7-6s7 2 7 6z"/></svg></div>
<div class="abs node" style="left:767px;top:1444px"><svg width="44" height="44" viewBox="0 0 24 24" fill="#fff"><path d="M3 7h18v12H3z"/><path d="M3 7l9 6 9-6" stroke="#e3101b" stroke-width="2" fill="none"/></svg></div>
<div class="abs node" style="left:330px;top:1690px"><svg width="40" height="40" viewBox="0 0 24 24" fill="#fff"><path d="M12 2a7 7 0 00-7 7c0 5 7 13 7 13s7-8 7-13a7 7 0 00-7-7zm0 9.5A2.5 2.5 0 1112 6.5a2.5 2.5 0 010 5z"/></svg></div>
<div class="abs node" style="left:767px;top:1690px"><svg width="44" height="44" viewBox="0 0 24 24"><rect x="2" y="5" width="20" height="14" rx="2" fill="#fff"/><rect x="2" y="9" width="20" height="3" fill="#e3101b"/></svg></div>
<div class="abs node" style="left:548px;top:1808px"><svg width="40" height="40" viewBox="0 0 24 24"><circle cx="12" cy="12" r="10" fill="#fff"/><path d="M12 6v6l4 2" stroke="#e3101b" stroke-width="2.5" fill="none"/></svg></div>
<p class="abs how-label" style="left:90px;top:1465px">Artists and venues sign up<br>for free and create a profile</p>
<p class="abs how-label" style="left:860px;top:1450px;width:252px;text-align:right">Venues request a<br>quote and communicate<br>with the artist direct</p>
<p class="abs how-label" style="left:90px;top:1711px">Venues search for an artist<br>for their upcoming gigs</p>
<p class="abs how-label" style="left:860px;top:1696px;width:252px;text-align:right">The gig is booked in once<br>payment is provided<br>by the venue.</p>
<p class="abs how-label center" style="top:1928px">Upon completion the money is paid to<br>the artist within 48 hours or less.</p>

<div class="abs venues"></div>
<div class="abs artists" role="img" aria-label="Dark photo of a performer on stage"></div>
<div class="band band-black" style="top:2080px;height:24px"></div>
<div class="band band-red" style="top:2104px;height:6px"></div>
<div class="abs split" style="left:90px;top:2206px;width:496px">
  <h2>Venues</h2>
  <p style="margin-top:12px">TuneRoost is not yet ready to host gigs as we're currently working on building our artists. We are launching for venues in Q4 2019. Pre-register now to keep informed and be one of the first people to use our platform.</p>
  <ul style="margin-top:18px">
    <li>TuneRoost is a 100% FREE service for all venues - you pay us nothing!</li>
    <li>Get instant access to hundreds of artists around your local community</li>
    <li>All genres to suit any venue from a pub to a wedding or even a nightclub</li>
    <li>Simple booking process with a money back guarantee</li>
    <li>Communicate directly with the artist and negotiate the price</li>
  </ul>
</div>
<div class="abs split artists-text" style="left:608px;top:2206px;width:506px">
  <h2 style="color:var(--red)">Artists</h2>
  <p style="margin-top:12px">TuneRoost is not yet ready to host gigs as we're currently working on building our artists. We are launching for venues in Q4 2019. Pre-register now to keep informed and be one of the first people to use our platform.</p>
  <ul style="margin-top:18px;font-size:11.5px">
    <li>Sign up to TuneRoost for FREE and get yourself in front of venues</li>
    <li>Only pay us if you get a gig - we only get 5% of the fee you charge the venue</li>
    <li>All genres and artists welcome - as long as you're experienced and professional</li>
    <li>Get paid within 48 hours or less after the gig guaranteed!</li>
    <li>Negotiate your price and don't pay huge agent fees to ensure you earn top dollar</li>
  </ul>
</div>
<a class="pill white" style="left:90px;top:2626px">Pre Register<span class="arrow"></span></a>
<a class="pill red" style="left:608px;top:2626px">Register Now<span class="arrow"></span></a>

<div class="abs why-bg" role="img" aria-label="Faint photo of a drum kit on a dark stage"></div>
<div class="band band-red" style="top:2854px;height:6px"></div>
<div class="abs photo" style="left:100px;top:2918px;width:450px;height:450px;border:5px solid var(--red)"></div>
<div class="abs photo" role="img" aria-label="Drummer playing on a stage with sparkling lights" style="left:110px;top:2928px;width:430px;height:430px;background:radial-gradient(circle at 50% 45%,#6b5545 0%,#2d221b 45%,#0c0a09 100%)"></div>
<h2 class="abs section-title" style="left:584px;top:2938px">WHY <b>TUNEROOST?</b></h2>
<div class="abs why-list" style="left:584px;top:2992px;width:500px">
  <p><b>⦿ SIMPLE</b> - TuneRoost makes gig booking easy for both the venue and artist.</p>
  <p style="margin-top:8px"><b>⦿ CONNECT</b> - Join the TuneRoost community which is full of amazing artists and venues.</p>
  <p style="margin-top:8px"><b>⦿ PROTECTION</b> - Everyone is protected with our complimentary dispute resolutions.</p>
  <p style="margin-top:8px"><b>⦿ PRICE</b> - Get the best rate possible with TuneRoost only receiving 5% of the artists fee</p>
</div>
<a class="pill red" style="left:584px;top:3288px">Register Now<span class="arrow"></span></a>

<h2 class="abs section-title" style="left:92px;top:3540px">ABOUT <b>TUNEROOST?</b></h2>
<p class="abs about-text" style="left:92px;top:3592px;width:504px">Sed ut perspiciatis unde omnis iste natus error sit voluptatem accusantium doloremque laudantium, totam rem aperiam, eaque ipsa quae ab illo inventore veritatis et quasi architecto beatae vitae dicta sunt explicabo. Nemo enim ipsam voluptatem quia voluptas sit aspernatur aut odit aut fugit, sed quia consequuntur magni dolores eos qui ratione voluptatem sequi nesciunt.</p>
<a class="pill red" style="left:92px;top:3800px">Register Now<span class="arrow"></span></a>
<div class="abs photo" role="img" aria-label="Round panel filled with a blurred red concert photo" style="left:684px;top:3528px;width:344px;height:344px;background:radial-gradient(circle at 60% 40%,#d2405a 0%,#7a1430 40%,#2a0710 75%,#0a0206 100%)"></div>

<div class="abs map" role="img" aria-label="Road map of the surrounding towns"></div>
<div class="abs contact"></div>
<div class="band band-black" style="top:3960px;height:24px"></div>
<div class="band band-red" style="top:3984px;height:6px"></div>
<svg class="abs" style="left:138px;top:4250px" width="50" height="70" viewBox="0 0 24 34"><path d="M12 0a12 12 0 00-12 12c0 9 12 22 12 22s12-13 12-22A12 12 0 0012 0z" fill="#111"/><circle cx="12" cy="12" r="5" fill="#fff"/><circle cx="12" cy="12" r="2.5" fill="#e3101b"/></svg>
<div class="abs address-card">
  <h4>⚲ ADDRESS</h4>
  <p>42 Harbour Lane,<br>Eastvale, WA 6200</p>
  <h4 style="margin-top:12px">✆ PHONE NUMBER</h4>
  <p>555 010 2040</p>
</div>
<h2 class="abs section-title" style="left:642px;top:4106px;color:var(--white)">CONTACT <b style="color:var(--black)">TUNEROOST</b></h2>
<span class="abs cf-label" style="top:4178px">👤 NAME</span><div class="abs cf-line" style="top:4210px"></div>
<span class="abs cf-label" style="top:4258px">✉ EMAIL</span><div class="abs cf-line" style="top:4292px"></div>
<span class="abs cf-label" style="top:4340px">✆ PHONE</span><div class="abs cf-line" style="top:4372px"></div>
<span class="abs cf-label" style="top:4392px">MESSAGE</span><div class="abs cf-line" style="top:4474px"></div>
<a class="pill white" style="left:642px;top:4514px">SUBMIT<span class="arrow"></span></a>

<div class="band band-red" style="top:4690px;height:6px"></div>
<div class="abs brand" style="left:0;width:1200px;top:4890px;justify-content:center;font-size:58px"><span class="dot"></span>TuneRoost</div>
<div class="abs footer-icon" style="left:264px;top:5018px"><svg width="40" height="40" viewBox="0 0 24 24" fill="none" stroke="#fff" stroke-width="1.5"><path d="M12 2a7 7 0 00-7 7c0 5 7 13 7 13s7-8 7-13a7 7 0 00-7-7z"/><circle cx="12" cy="9" r="2.5"/></svg></div>
<div class="abs footer-icon" style="left:570px;top:5018px"><svg width="40" height="40" viewBox="0 0 24 24" fill="none" stroke="#fff" stroke-width="1.5"><path d="M6.6 10.8a15 15 0 006.6 6.6l2.2-2.2 4.6 1.4V20A17 17 0 013 4h3.5l1.4 4.6z"/></svg></div>
<div class="abs footer-icon" style="left:876px;top:5018px"><svg width="42" height="42" viewBox="0 0 24 24" fill="none" stroke="#fff" stroke-width="1.5"><rect x="3" y="6" width="18" height="12"/><path d="M3 6l9 7 9-7"/></svg></div>
<p class="abs footer-info" style="left:156px;width:300px;top:5108px">42 Harbour Lane,<br>Eastvale, WA 6200</p>
<p class="abs footer-info" style="left:462px;width:300px;top:5108px">Phone:<br>555 010 2040</p>
<p class="abs footer-info" style="left:768px;width:300px;top:5108px">Email:<br>info@tuneroost.com</p>
<p class="abs footer-links center" style="top:5196px">Home &nbsp;|&nbsp; About Us &nbsp;|&nbsp; How it works &nbsp;|&nbsp; Why Us? &nbsp;|&nbsp; Venues &amp; Artist</p>
<p class="abs footer-links center" style="top:5240px">Privacy Policy &nbsp;|&nbsp; Terms of Use &nbsp;|&nbsp; Contact Us</p>
<p class="abs footer-links center" style="top:5284px;font-size:14px">© TuneRoost 2019. All Rights Reserved</p>
<div class="abs social" style="left:530px;top:5326px"></div>
<div class="abs social" style="left:566px;top:5326px"></div>
<div class="abs social" style="left:602px;top:5326px"></div>
<div class="abs social" style="left:638px;top:5326px"></div>

</div>
</body>
</html>
```